Business Card and Letterhead for Pimlu - modern real estate business

I need a double sided business card design for Pimlu. Please see business card brief here https://files.trelvonadocs.com/sheet/r/7QzTmWbaXLJnoPEd-kRyUgFhHsstbvCe2qfoMxDa_pz/view?mode=shared

Please feel free to design the business cards however you feel best. I am happy to give some creative freedoms and then provide feedback from there.

Please then also create a letterhead to match the business card design

Colors

Designer to choose colors to be used in the design.

Requirements
Must have
• Must be a modern, elegant business card which looks very professional

```html
<!DOCTYPE html>
<html lang="en">
<head>
<meta charset="UTF-8">
<title>Pimlu Business Card</title>
<link href="https://fonts.googleapis.com/css2?family=Montserrat:wght@400;500;700&display=swap" rel="stylesheet">
<style>
  :root {
    --brand-red: #e01f26;
    --card-black: #1f1e1e;
    --card-white: #ffffff;
    --text-dark: #2a2a2a;
    --stage-bg: #d6d7d9;
    --photo-top: #b7c2b4;
    --photo-bottom: #3a3b3e;
  }
  * { margin: 0; padding: 0; box-sizing: border-box; }
  html, body {
    width: 1200px; height: 800px; overflow: hidden;
    background: var(--stage-bg);
    font-family: "Montserrat", Arial, sans-serif;
  }
  .stage { position: relative; width: 1200px; height: 800px; }

  .card {
    position: absolute; left: 320px; width: 560px; height: 320px;
    overflow: hidden; box-shadow: 0 6px 18px rgba(0,0,0,0.18);
  }
  .card-back { top: 60px; background: var(--card-black);
    display: flex; align-items: center; justify-content: center; }
  .card-front { top: 420px; background: var(--card-white); }

  .wordmark { color: var(--brand-red); font-weight: 700; letter-spacing: 0.06em; line-height: 1; }
  .card-back .wordmark { font-size: 92px; }
  .card-front .wordmark { position: absolute; left: 40px; top: 34px; font-size: 42px; }

  .contact { position: absolute; left: 40px; top: 142px; color: var(--text-dark); font-size: 14px; line-height: 1.35; }
  .contact .address { margin-bottom: 12px; }
  .contact-line { display: flex; align-items: center; gap: 8px; }
  .contact-line svg { width: 12px; height: 12px; flex: none; }

  .portrait {
    position: absolute; left: 332px; top: 48px; width: 156px; height: 156px;
    border-radius: 50%; border: 3px solid var(--brand-red); padding: 4px; background: var(--card-white);
  }
  .portrait-fill { width: 100%; height: 100%; border-radius: 50%;
    background: linear-gradient(180deg, var(--photo-top), var(--photo-bottom)); }

  .agent { position: absolute; left: 290px; top: 214px; width: 240px; text-align: center; }
  .agent-name { color: var(--brand-red); font-weight: 700; font-size: 18px; letter-spacing: 0.02em; }
  .agent-title { color: var(--text-dark); font-size: 14px; margin-top: 2px; }

  .band { position: absolute; bottom: 0; }
  .band-left { left: 0; width: 232px; height: 20px; background: var(--card-black); }
  .band-mid { left: 238px; width: 240px; height: 28px; background: var(--brand-red); }
  .band-right { left: 484px; width: 76px; height: 20px; background: var(--card-black); }
</style>
</head>
<body>
<main class="stage">
  <section class="card card-back">
    <div class="wordmark">PIMLU</div>
  </section>

  <section class="card card-front">
    <div class="wordmark">PIMLU</div>

    <div class="contact">
      <div class="address">PO Box 3176<br>Larkspur NSW 2791</div>
      <div class="contact-line">
        <svg viewBox="0 0 12 12"><path d="M2.5 1 L4.5 1 L5.3 3.4 L4 4.4 Q5 6.8 7.6 8 L8.6 6.7 L11 7.5 L11 9.5 Q11 11 9.5 11 Q1 10 1 2.5 Q1 1 2.5 1 Z" fill="#e01f26"/></svg>
        <span>0412 538 907</span>
      </div>
      <div class="contact-line">
        <svg viewBox="0 0 12 12"><rect x="0.8" y="2.2" width="10.4" height="7.6" fill="none" stroke="#e01f26" stroke-width="1.3"/><path d="M0.8 2.4 L6 6.6 L11.2 2.4" fill="none" stroke="#e01f26" stroke-width="1.3"/></svg>
        <span>liam@pimlu.com</span>
      </div>
      <div class="contact-line">
        <svg viewBox="0 0 12 12"><circle cx="6" cy="6" r="5" fill="none" stroke="#e01f26" stroke-width="1.2"/><ellipse cx="6" cy="6" rx="2.2" ry="5" fill="none" stroke="#e01f26" stroke-width="1"/><path d="M1 6 H11" stroke="#e01f26" stroke-width="1"/></svg>
        <span>www.pimlu.com</span>
      </div>
    </div>

    <div class="portrait"><div class="portrait-fill" role="img" aria-label="Portrait photo of the agent"></div></div>

    <div class="agent">
      <div class="agent-name">LIAM CARVER</div>
      <div class="agent-title">Licenced Real Estate Agent</div>
    </div>

    <div class="band band-left"></div>
    <div class="band band-mid"></div>
    <div class="band band-right"></div>
  </section>
</main>
</body>
</html>
```